Management consulting Company in the electronic payment ecosystem needs a Website

We need to have a "showcase" style website that contains the key message that our company is able to provide management consulting in the world of payment systems. Our mission is to assist our clients in reviewing their sales, purchasing, operation and IT processes and to support them in identifying the best solution in the use of payment systems.

```html
<!DOCTYPE html>
<html lang="en">
<head>
<meta charset="utf-8">
<title>Tillwise Consulting</title>
<link href="https://fonts.googleapis.com/css2?family=Lato:ital,wght@0,400;0,700;0,900;1,400&family=Nunito+Sans:wght@800&display=swap" rel="stylesheet">
<style>
:root{
  --navy:#0b1858;
  --navy-deep:#081246;
  --orange:#f7941d;
  --ink:#1d1d2b;
  --text:#4a4a55;
  --grey:#f2f2f2;
  --line:#d9d9d9;
  --footer:#222226;
  --white:#ffffff;
}
*{margin:0;padding:0;box-sizing:border-box}
html,body{width:1200px;height:5282px;overflow:hidden}
body{position:relative;font-family:"Lato",sans-serif;color:var(--text);background:var(--white)}
.abs{position:absolute}
.btn{position:absolute;display:flex;align-items:center;justify-content:center;background:var(--orange);color:var(--white);font-weight:700;font-size:12px;letter-spacing:.5px;border-radius:20px;text-transform:uppercase;height:36px}
.heading{font-weight:900;color:var(--navy);text-transform:uppercase;font-size:27px;letter-spacing:.3px}
.center{text-align:center;left:0;width:1200px}
p{line-height:1.85}

/* header */
.site-header{top:0;left:0;width:1200px;height:117px;background:var(--white)}
.brand{left:95px;top:22px;display:flex;align-items:center;gap:10px}
.brand-dot{width:66px;height:66px;border-radius:50%;background:var(--navy)}
.brand-name{font-weight:900;font-size:36px;color:var(--navy);line-height:1}
.nav{right:58px;top:45px;display:flex;gap:18px;align-items:center;font-size:13px;font-weight:700;color:var(--ink)}
.nav a{color:inherit;text-decoration:none;padding:6px 10px}
.nav .active{background:var(--orange);color:var(--white);border-radius:16px;padding:7px 20px}

/* hero */
.hero-photo{top:117px;left:0;width:1200px;height:615px;background:linear-gradient(100deg,#3b3f47 0%,#6d6b6a 35%,#a7a099 60%,#cfc8c0 100%)}
.hero-title{left:96px;top:262px;color:var(--white);font-weight:900;font-size:46px;line-height:1.15}
.hero-text{left:96px;top:375px;width:480px;color:var(--white);font-size:19px;line-height:1.6}
.hero-wave{left:0;top:600px}

/* trust */
.trust-title{top:796px;font-weight:700;font-size:14px;color:var(--ink);letter-spacing:.3px}
.clients{top:848px;left:148px;width:904px;display:flex;align-items:center;justify-content:space-between}
.clients .client{font-weight:700;font-size:15px;color:#555;width:110px;text-align:center}
.arrow{font-size:22px;color:#666}

/* mission */
.mission{top:1000px;left:0}
.mission-title{top:1082px;color:var(--white)}
.mission-quote{top:1128px;left:150px;width:900px;text-align:center;color:var(--white);font-style:italic;font-size:23px;line-height:1.95}

/* solutions */
.sol-title{top:1440px}
.sol-intro{top:1492px;left:200px;width:800px;text-align:center;font-size:13px;line-height:1.9}
.sol-grid{top:1600px;left:190px;width:840px;height:350px;display:grid;grid-template-columns:1fr 1fr 1fr;grid-template-rows:1fr 1fr}
.sol-cell{display:flex;flex-direction:column;align-items:center;justify-content:center;gap:20px;font-weight:700;font-size:15px;color:var(--navy)}
.sol-cell:nth-child(3n+1),.sol-cell:nth-child(3n+2){border-right:1px solid var(--line)}
.sol-cell:nth-child(-n+3){border-bottom:1px solid var(--line)}

/* about */
.about-bg{top:2017px;left:0;width:610px;height:455px;background:var(--grey)}
.about-photo{top:2017px;left:610px;width:590px;height:455px;background:linear-gradient(135deg,#1a1f2c,#4b5469 55%,#c7ccd8)}
.about-title{left:95px;top:2080px;font-size:25px}
.about-text{left:95px;top:2132px;width:490px;font-size:13px}
.about-text p+p{margin-top:14px}

/* features */
.feat-art{background:linear-gradient(135deg,#e9ecef,#dfe5ea)}
.feat-title{font-family:"Nunito Sans",sans-serif;font-weight:800;color:var(--navy);font-size:31px;line-height:1.15}
.feat-text{font-size:13px;line-height:2.35;width:550px}

/* testimonial */
.testi{top:3410px;left:0}
.testi-title{top:3530px;color:var(--white)}
.testi-quote{top:3590px;left:200px;width:800px;text-align:center;color:var(--white);font-style:italic;font-size:20px;line-height:1.8}
.testi-name{top:3717px;color:var(--orange);font-weight:700;font-size:13px}

/* blog */
.blog-title{top:3918px}
.post{top:3988px;width:495px;height:337px;display:flex;align-items:flex-end;padding:0 24px 28px;color:var(--white);font-size:22px;line-height:1.4}

/* questions */
.faq{top:4505px;left:0;width:1200px;height:392px;background:var(--navy-deep)}
.faq-title{top:4608px;color:var(--white)}
.faq-sub{top:4652px;color:var(--white);font-size:19px}
.card{top:4705px;width:268px;height:242px;background:var(--white);border-radius:14px;box-shadow:0 4px 14px rgba(0,0,0,.15);display:flex;flex-direction:column;align-items:center;padding-top:28px;text-align:center}
.card h4{margin-top:14px;font-size:16px;color:var(--navy);font-weight:900}
.card small{display:block;margin-top:8px;font-size:11px;line-height:1.7;color:#666;width:200px}
.card .strong{font-weight:700;color:var(--ink);font-size:13px;line-height:1.9;margin-top:6px}
.card .btn{position:static;margin-top:auto;margin-bottom:30px;width:180px;height:34px;font-size:12px;text-transform:none}

/* footer */
.site-footer{top:4897px;left:0;width:1200px;height:385px;background:var(--footer)}
.foot-brand{left:95px;top:5013px;display:flex;align-items:center;gap:10px}
.foot-brand .brand-dot{width:56px;height:56px;background:#7a7a80}
.foot-brand .brand-name{color:#b6b6bc;font-size:30px}
.foot-about{left:95px;top:5088px;width:290px;color:#cfcfd4;font-size:11px;line-height:1.9}
.foot-col{top:5008px;color:var(--white)}
.foot-col h5{font-size:13px;font-weight:700;margin-bottom:14px;text-transform:uppercase}
.foot-col ul{list-style:none;font-size:11px;line-height:2.6;color:#d5d5da}
.foot-links{display:grid;grid-template-columns:80px 80px}
.newsletter input{display:block;width:210px;height:34px;border-radius:18px;border:none;padding:0 16px;font-family:inherit;font-size:10px;margin-bottom:10px}
.newsletter .btn{position:static;width:210px;height:34px}
.foot-rule{top:5206px;left:95px;width:1010px;height:1px;background:#3b3b40}
.copyright{top:5240px;left:95px;font-size:10px;color:#cfcfd4}
.socials{top:5234px;left:928px;display:flex;gap:22px}
.socials span{width:20px;height:20px;border-radius:50%;background:var(--white)}
</style>
</head>
<body>

<header class="abs site-header">
  <div class="abs brand"><span class="brand-dot"></span><span class="brand-name">Tillwise</span></div>
  <nav class="abs nav">
    <a class="active">HOME</a><a>ABOUT US</a><a>SERVICES</a><a>SOLUTIONS</a><a>BLOG</a><a>CONTACT US</a>
  </nav>
</header>

<section>
  <div class="abs hero-photo" role="img" aria-label="Photo of a smiling woman in a cardigan sitting by a window, using her smartphone"></div>
  <h1 class="abs hero-title">WELCOME TO<br>TILLWISE CONSULTING</h1>
  <p class="abs hero-text">Sed ut perspiciatis unde omnis iste natus error sit voluptatem accusantium doloremque laudantium, totam rem aperiam, eaque ipsa quae ab illo inventore veritatis et quasi architecto.</p>
  <a class="btn" style="left:96px;top:518px;width:180px">Read more</a>
  <svg class="abs hero-wave" width="1200" height="140" viewBox="0 0 1200 140" preserveAspectRatio="none">
    <path d="M0 125 C250 80 420 20 650 55 C860 88 1020 90 1200 20 L1200 140 L0 140 Z" fill="#ffffff"/>
  </svg>
</section>

<section>
  <div class="abs center trust-title">OVER 1000 TRUSTED CUSTOMERS</div>
  <div class="abs clients">
    <span class="arrow">&#8249;</span>
    <span class="client">Lorvane</span>
    <span class="client">Kestrel</span>
    <span class="client">Brightfold</span>
    <span class="client">Dravia</span>
    <span class="client">Mellow &amp; Co</span>
    <span class="client">Ostrand</span>
    <span class="arrow">&#8250;</span>
  </div>
</section>

<section>
  <svg class="abs mission" width="1200" height="375" viewBox="0 0 1200 375" preserveAspectRatio="none">
    <path d="M0 0 C250 30 480 40 700 15 C900 -5 1050 0 1200 10 L1200 325 C980 300 760 345 560 350 C330 356 150 330 0 370 Z" fill="#0b1858"/>
  </svg>
  <h2 class="abs center heading mission-title">OUR MISSION</h2>
  <p class="abs mission-quote">“Our mission is to assist our clients in reviewing their sales, purchasing, operation and IT processes and to support them in identifying the best solution in the use of payment systems..”</p>
</section>

<section>
  <h2 class="abs center heading sol-title">OUR SOLUTIONS</h2>
  <p class="abs sol-intro">Sed ut perspiciatis unde omnis iste natus error sit voluptatem accusantium doloremque laudantium, totam rem aperiam, eaque ipsa quae ab illo inventore veritatis et quasi architecto..</p>
  <div class="abs sol-grid">
    <div class="sol-cell">
      <svg width="64" height="64" viewBox="0 0 64 64" fill="none" stroke="#0b1858" stroke-width="2"><rect x="6" y="22" width="52" height="34"/><path d="M6 22 L32 42 L58 22"/><rect x="16" y="8" width="32" height="24" stroke="#f7941d"/></svg>
      Temporibus autem</div>
    <div class="sol-cell">
      <svg width="64" height="64" viewBox="0 0 64 64" fill="none" stroke="#0b1858" stroke-width="2"><rect x="8" y="10" width="40" height="28"/><rect x="4" y="38" width="48" height="6"/><rect x="42" y="26" width="16" height="28" stroke="#f7941d"/><rect x="14" y="44" width="18" height="14"/></svg>
      Temporibus autem</div>
    <div class="sol-cell">
      <svg width="64" height="64" viewBox="0 0 64 64" fill="none" stroke="#0b1858" stroke-width="2"><rect x="8" y="40" width="9" height="18"/><rect x="22" y="32" width="9" height="26"/><rect x="36" y="24" width="9" height="34"/><rect x="50" y="16" width="9" height="42"/><path d="M6 34 L26 20 L38 26 L56 8" stroke="#f7941d"/></svg>
      Temporibus autem</div>
    <div class="sol-cell">
      <svg width="64" height="64" viewBox="0 0 64 64" fill="none" stroke="#0b1858" stroke-width="2"><rect x="10" y="6" width="34" height="50" rx="3"/><rect x="15" y="11" width="24" height="10" stroke="#f7941d"/><path d="M16 28h6M26 28h6M16 36h6M26 36h6M16 44h6M26 44h6"/><path d="M40 40 c6 0 12 6 12 14 v6" /></svg>
      Temporibus autem</div>
    <div class="sol-cell">
      <svg width="64" height="64" viewBox="0 0 64 64" fill="none" stroke="#0b1858" stroke-width="2"><circle cx="24" cy="26" r="14"/><circle cx="24" cy="26" r="5"/><circle cx="46" cy="44" r="10" stroke="#f7941d"/><circle cx="46" cy="44" r="3" stroke="#f7941d"/></svg>
      Temporibus autem</div>
    <div class="sol-cell">
      <svg width="64" height="64" viewBox="0 0 64 64" fill="none" stroke="#0b1858" stroke-width="2"><rect x="8" y="22" width="44" height="34" rx="2"/><rect x="22" y="6" width="20" height="28" transform="rotate(20 32 20)" stroke="#f7941d"/><rect x="40" y="34" width="14" height="10"/></svg>
      Temporibus autem</div>
  </div>
</section>

<section>
  <div class="abs about-bg"></div>
  <div class="abs about-photo" role="img" aria-label="Photo of hands holding a tablet showing business charts, pointing with a pen"></div>
  <h2 class="abs heading about-title">ABOUT TILLWISE CONSULTING</h2>
  <div class="abs about-text">
    <p>Sed ut perspiciatis unde omnis iste natus error sit voluptatem accusantium doloremque laudantium, totam rem aperiam, eaque ipsa quae ab illo inventore veritatis et quasi architecto..</p>
    <p>Nemo enim ipsam voluptatem quia voluptas sit aspernatur aut odit aut fugit, sed quia consequuntur magni dolores eos qui ratione voluptatem sequi nesciunt. Neque porro quisquam est, qui dolorem ipsum quia dolor sit amet, consectetur, adipisci velit, sed quia non numquam eius modi tempora incidunt ut labore et dolore magnam aliquam quaerat voluptatem.</p>
  </div>
  <a class="btn" style="left:95px;top:2366px;width:182px">Read more</a>
</section>

<section>
  <div class="abs feat-art" style="left:0;top:2515px;width:470px;height:430px;border-radius:0 200px 200px 0" role="img" aria-label="Illustration of two colleagues meeting at a round table with a laptop and tablet"></div>
  <h3 class="abs feat-title" style="left:542px;top:2585px">Neque porro quisquam est,<br>qui dolorem ipsum quia<br>dolor sit amet</h3>
  <p class="abs feat-text" style="left:542px;top:2700px">Nemo enim ipsam voluptatem quia voluptas sit aspernatur aut odit aut fugit, sed quia consequuntur magni dolores eos qui ratione voluptatem sequi nesciunt. Neque porro quisquam est, qui dolorem ipsum quia dolor sit amet, consectetur non numquam eius modi tempora incidunt ut labore.</p>
  <a class="btn" style="left:542px;top:2850px;width:182px">Read more</a>

  <h3 class="abs feat-title" style="left:96px;top:3000px">Neque porro quisquam est,<br>qui dolorem ipsum quia<br>dolor sit amet</h3>
  <p class="abs feat-text" style="left:96px;top:3117px">Nemo enim ipsam voluptatem quia voluptas sit aspernatur aut odit aut fugit, sed quia consequuntur magni dolores eos qui ratione voluptatem sequi nesciunt. Neque porro quisquam est, qui dolorem ipsum quia dolor sit amet, consectetur non numquam eius modi tempora incidunt ut labore.</p>
  <a class="btn" style="left:96px;top:3267px;width:182px">Read more</a>
  <div class="abs feat-art" style="left:735px;top:2950px;width:465px;height:415px;border-radius:200px 0 0 200px;background:linear-gradient(135deg,#eef0f6,#d8dcef 45%,#f2c9d6 70%,#cfe0f5)" role="img" aria-label="Illustration of two businessmen studying colourful 3D data charts and dashboards"></div>
</section>

<section>
  <svg class="abs testi" width="1200" height="465" viewBox="0 0 1200 465" preserveAspectRatio="none">
    <path d="M0 25 C200 0 380 -5 560 15 C760 40 980 20 1200 0 L1200 460 C950 440 700 445 450 455 C250 462 100 455 0 460 Z" fill="#0b1858"/>
  </svg>
  <h2 class="abs center heading testi-title">WHAT OUR CLIENT SAYS</h2>
  <span class="abs" style="left:72px;top:3636px;color:#fff;font-size:26px">&#8249;</span>
  <span class="abs" style="left:1116px;top:3636px;color:#fff;font-size:26px">&#8250;</span>
  <p class="abs testi-quote">“ Sed ut perspiciatis unde omnis iste natus error sit voluptatem accusantium doloremque laudantium, totam rem aperiam, eaque ipsa quae ab illo inventore veritatis et quasi architecto beatae vitae dicta sunt explicabo...”</p>
  <div class="abs center testi-name">NAME HEADING</div>
</section>

<section>
  <h2 class="abs center heading blog-title">BLOG POSTS</h2>
  <article class="abs post" style="left:95px;background:linear-gradient(180deg,#2a2530 0%,#1b1a22 55%,#0d0d12 100%)" role="img" aria-label="Photo of a hand holding a smartphone with glowing app icons">
    <span>Neque porro quisquam est, qui dolorem ipsum quia saepe eveniet..</span>
  </article>
  <article class="abs post" style="left:612px;background:linear-gradient(180deg,#8d8a86 0%,#5c5350 55%,#1c1b1e 100%)" role="img" aria-label="Photo of a smiling couple looking at a laptop together">
    <span>Neque porro quisquam est, qui dolorem ipsum quia saepe eveniet..</span>
  </article>
  <a class="btn" style="left:510px;top:4390px;width:180px;height:34px;text-transform:uppercase">Read all posts</a>
</section>

<section>
  <div class="abs faq"></div>
  <svg class="abs" style="left:0;top:4490px" width="1200" height="60" viewBox="0 0 1200 60" preserveAspectRatio="none">
    <path d="M0 0 L1200 0 L1200 15 C900 45 600 0 300 20 C180 28 80 28 0 20 Z" fill="#ffffff"/>
  </svg>
  <h2 class="abs center heading faq-title">DO YOU HAVE ANY QUESTIONS?</h2>
  <div class="abs center faq-sub">Nemo enim ipsam voluptatem quia voluptas sit aspernatur aut odit aut fugit,.</div>

  <div class="abs card" style="left:173px">
    <svg width="40" height="48" viewBox="0 0 40 48"><path d="M20 2 C9 2 2 10 2 19 C2 32 20 46 20 46 C20 46 38 32 38 19 C38 10 31 2 20 2 Z" fill="#0b1858"/><circle cx="20" cy="19" r="7" fill="#fff"/></svg>
    <h4>Address Info</h4>
    <small>Nam libero tempore, cum soluta nobis debitis aut rerum</small>
    <a class="btn">Map Direction</a>
  </div>
  <div class="abs card" style="left:466px">
    <svg width="44" height="48" viewBox="0 0 44 48"><path d="M10 6 L18 6 L21 16 L16 20 C18 27 22 31 28 34 L32 29 L42 32 L42 40 C42 44 38 46 34 45 C18 41 6 28 4 12 C4 8 6 6 10 6 Z" fill="#0b1858"/></svg>
    <h4>Contact Us</h4>
    <div class="strong">1-800-555-0142<br>hello@tillwise.example</div>
    <a class="btn">Contact Us</a>
  </div>
  <div class="abs card" style="left:759px">
    <svg width="52" height="44" viewBox="0 0 52 44"><ellipse cx="20" cy="16" rx="18" ry="13" fill="#0b1858"/><path d="M8 26 L4 36 L16 28 Z" fill="#0b1858"/><ellipse cx="36" cy="26" rx="14" ry="10" fill="#0b1858" stroke="#fff" stroke-width="2"/></svg>
    <h4>Customer Support</h4>
    <small>Nam libero tempore, cum soluta nobis debitis aut rerum</small>
    <a class="btn">Chat Us</a>
  </div>
</section>

<footer class="abs site-footer" style="z-index:-1"></footer>
<div class="abs foot-brand"><span class="brand-dot"></span><span class="brand-name">Tillwise</span></div>
<p class="abs foot-about">Nemo enim ipsam voluptatem quia voluptas sit aspernatur aut odit aut fugit, sed quia consequuntur magni dolores eos qui ratione voluptatem sequi nesciunt.</p>
<div class="abs foot-col" style="left:420px">
  <h5>Quick Links</h5>
  <ul class="foot-links"><li>Home</li><li>Blog</li><li>About Us</li><li>Contact</li><li>Services</li><li>Imprint</li><li>Solutions</li></ul>
</div>
<div class="abs foot-col" style="left:636px">
  <h5>Resources</h5>
  <ul><li>Nemo enim ipsam</li><li>Voluptatem quia</li><li>Voluptas sit aspernatur aut</li><li>Odit aut fugit,</li></ul>
</div>
<div class="abs foot-col newsletter" style="left:858px">
  <h5>Newsletter</h5>
  <input type="text" placeholder="Enter Email Address">
  <a class="btn">Subscribe Now</a>
</div>
<div class="abs foot-rule"></div>
<div class="abs copyright">Copyright © 2021, Tillwise Consulting All Right reserved.</div>
<div class="abs socials" aria-label="Social links"><span></span><span></span><span></span><span></span><span></span></div>

</body>
</html>
```